Mastering Modern Vineyard Management

size of the ad - 8”x 10.75" plus 0.25" bleed
I would like an ad for a magazine that will stand out and make people want to read the ad.
The ad should not be crowded and people reading the ad will be able to read the text.
I would like it to be a creative and modern-day design.
the list of topics should not be the focus of the ad.
the text is attached.
If you decide to use people in the ad then please no ladies.
please note that leave over 1 inch for the bottom of the footer

```html
<!DOCTYPE html>
<html lang="en">
<head>
<meta charset="utf-8">
<title>Vineyard Management Course – Magazine Ad</title>
<link href="https://fonts.googleapis.com/css2?family=Bebas+Neue&family=Montserrat:wght@300;400;500;600;700&display=swap" rel="stylesheet">
<style>
  :root {
    --page: #f4f4f4;
    --paper: #ffffff;
    --ink: #141414;
    --navy: #1c2a5a;
    --navy-deep: #1a2550;
    --blue: #2a9ad8;
    --band-dark: #232325;
    --footer-blue: #a5c8e6;
    --footer-line: #b9d4ec;
    --body-text: #333333;
  }
  html, body {
    margin: 0;
    padding: 0;
    width: 1200px;
    height: 2400px;
    overflow: hidden;
    background: var(--page);
  }
  .ad {
    position: absolute;
    left: 72px;
    top: 490px;
    width: 1057px;
    height: 1421px;
    background: var(--paper);
    box-shadow: 0 10px 30px rgba(0,0,0,0.18);
    overflow: hidden;
  }
  .ad-art { display: block; width: 1057px; height: 1421px; }
  .display { font-family: 'Bebas Neue', 'Oswald', sans-serif; }
  .sans { font-family: 'Montserrat', 'Helvetica Neue', Arial, sans-serif; }
  .course-title { fill: var(--ink); font-size: 138px; }
  .headline { fill: var(--blue); font-size: 70px; }
  .tagline { fill: #ffffff; font-size: 31px; font-weight: 400; }
  .location { fill: var(--navy); font-size: 46px; font-weight: 400; }
  .schedule { fill: var(--blue); font-size: 78px; font-weight: 700; }
  .session-strong { fill: var(--ink); font-size: 30px; font-weight: 700; }
  .session-light { fill: var(--ink); font-size: 30px; font-weight: 400; }
  .start-label { fill: var(--ink); font-size: 28px; font-weight: 400; }
  .start-month { fill: var(--ink); font-size: 64px; font-weight: 700; }
  .start-day { fill: #ffffff; font-size: 74px; }
  .start-suffix { fill: #ffffff; font-size: 36px; }
  .limited { fill: var(--ink); font-size: 24px; font-weight: 400; }
  .scholar-accent { fill: var(--blue); font-size: 36px; font-weight: 600; letter-spacing: 1px; }
  .scholar-main { fill: var(--ink); font-size: 36px; font-weight: 700; letter-spacing: 1px; }
  .early-bird { fill: var(--navy-deep); font-size: 36px; font-weight: 700; letter-spacing: 2px; }
  .special { fill: #ffffff; font-size: 50px; font-weight: 700; letter-spacing: 2px; }
  .audience { fill: #ffffff; font-size: 21px; font-weight: 700; }
  .topics-label { fill: var(--ink); font-size: 33px; font-weight: 600; }
  .topics-accent { fill: var(--blue); font-size: 33px; font-weight: 600; letter-spacing: 2px; }
  .topic { fill: var(--body-text); font-size: 21px; font-weight: 400; }
  .tick { fill: none; stroke: var(--blue); stroke-width: 3; stroke-linecap: round; stroke-linejoin: round; }
</style>
</head>
<body>
<div class="ad">
  <svg class="ad-art" viewBox="0 0 1057 1421" xmlns="http://www.w3.org/2000/svg">
    <defs>
      <linearGradient id="skylineTone" x1="0" y1="0" x2="1" y2="0">
        <stop offset="0" stop-color="#f3f5f8"/>
        <stop offset="0.35" stop-color="#dfe5ec"/>
        <stop offset="0.7" stop-color="#8fb4d6"/>
        <stop offset="1" stop-color="#3d86c6"/>
      </linearGradient>
      <linearGradient id="presenterTone" x1="0" y1="0" x2="0" y2="1">
        <stop offset="0" stop-color="#e9ecef"/>
        <stop offset="0.3" stop-color="#b7bcc3"/>
        <stop offset="0.55" stop-color="#2e3138"/>
        <stop offset="1" stop-color="#1b1d22"/>
      </linearGradient>
    </defs>

    <!-- hero visual -->
    <rect class="hero-visual" x="0" y="0" width="1057" height="451" fill="url(#skylineTone)" role="img" aria-label="Model towers in glass and blue rising over a growth chart"/>

    <!-- course title -->
    <g class="display course-title">
      <text x="54" y="168">VINEYARD</text>
      <text x="54" y="280">MANAGEMENT</text>
      <text x="54" y="392">COURSE</text>
    </g>

    <!-- headline band -->
    <polygon class="headline-band" points="0,451 1057,451 1057,627 552,627 520,599 0,599" fill="var(--band-dark)"/>
    <text class="display headline" x="62" y="542" textLength="917" lengthAdjust="spacingAndGlyphs">MASTERING MODERN VINEYARD MANAGEMENT</text>
    <text class="sans tagline" x="62" y="572" textLength="917" lengthAdjust="spacingAndGlyphs">INVESTING IN KNOWLEDGE IS INVESTING IN OPPORTUNITIES</text>

    <!-- early bird band -->
    <rect class="offer-band" x="0" y="879" width="1057" height="111" fill="var(--blue)"/>

    <!-- presenter visual -->
    <path class="presenter-visual" d="M700,584 Q760,570 800,600 Q830,660 820,720 L870,760 Q1000,790 1057,880 L1057,1284 L620,1284 L620,1060 Q650,900 700,860 Q740,800 730,740 Q690,680 700,584 Z" fill="url(#presenterTone)" role="img" aria-label="Instructor in a dark suit holding a small model house and pointing at it"/>

    <!-- location and schedule -->
    <text class="sans location" x="59" y="668">BROOKVALE</text>
    <line x1="372" y1="652" x2="690" y2="652" stroke="var(--navy)" stroke-width="2"/>
    <text class="sans schedule" x="57" y="746" textLength="444" lengthAdjust="spacingAndGlyphs">10-TUESDAY</text>
    <text class="sans session-strong" x="524" y="714">EVENINGS</text>
    <text class="sans session-light" x="524" y="745">SESSIONS</text>

    <text class="sans start-label" x="61" y="791">STARTING</text>
    <text class="sans start-month" x="59" y="852">FEB</text>
    <rect x="212" y="766" width="112" height="87" rx="12" fill="var(--blue)"/>
    <rect x="218" y="772" width="100" height="75" rx="9" fill="none" stroke="#ffffff" stroke-width="2"/>
    <text class="display start-day" x="230" y="836">28</text>
    <text class="display start-suffix" x="276" y="806">TH</text>

    <line x1="349" y1="773" x2="349" y2="847" stroke="#9a9a9a" stroke-width="2"/>
    <text class="sans limited" x="376" y="785">Limited</text>
    <text class="sans scholar-accent" x="376" y="819">PARTIAL</text>
    <text class="sans scholar-main" x="376" y="853">SCHOLARSHIPS</text>

    <!-- early bird offer -->
    <text class="sans early-bird" x="62" y="924">EARLY BIRD</text>
    <text class="sans special" x="62" y="969">SPECIAL</text>
    <text class="sans audience" x="317" y="917">FOR THOSE THAT STARTED</text>
    <text class="sans audience" x="317" y="941">OR WOULD LIKE TO GO</text>
    <text class="sans audience" x="317" y="966">INTO WINE GROWING</text>

    <!-- topics -->
    <text class="sans topics-label" x="78" y="1035">TOPICS:</text>
    <text class="sans topics-accent" x="229" y="1035">PARTIAL LISTING</text>
    <line x1="70" y1="1046" x2="545" y2="1046" stroke="var(--navy)" stroke-width="2"/>

    <g class="topic-list">
      <path class="tick" d="M70,1088 l5,6 l10,-12"/>
      <text class="sans topic" x="96" y="1095">Vineyard</text>
      <text class="sans topic" x="96" y="1120">planting strategies</text>
      <path class="tick" d="M70,1148 l5,6 l10,-12"/>
      <text class="sans topic" x="96" y="1155">Soil analysis</text>
      <path class="tick" d="M70,1183 l5,6 l10,-12"/>
      <text class="sans topic" x="96" y="1190">Irrigation</text>
      <path class="tick" d="M70,1218 l5,6 l10,-12"/>
      <text class="sans topic" x="96" y="1225">Canopy pruning</text>
      <path class="tick" d="M70,1253 l5,6 l10,-12"/>
      <text class="sans topic" x="96" y="1260">Harvest management</text>

      <path class="tick" d="M357,1088 l5,6 l10,-12"/>
      <text class="sans topic" x="380" y="1095">Vineyard</text>
      <text class="sans topic" x="380" y="1120">Legal basics</text>
      <path class="tick" d="M357,1148 l5,6 l10,-12"/>
      <text class="sans topic" x="380" y="1155">Sourcing vines</text>
      <path class="tick" d="M357,1183 l5,6 l10,-12"/>
      <text class="sans topic" x="380" y="1190">Pest control</text>
      <path class="tick" d="M357,1218 l5,6 l10,-12"/>
      <text class="sans topic" x="380" y="1225">Working with wineries</text>
      <path class="tick" d="M357,1253 l5,6 l10,-12"/>
      <text class="sans topic" x="380" y="1260">Tax fundamentals</text>
    </g>

    <!-- footer -->
    <rect class="footer-rule" x="0" y="1288" width="1057" height="7" fill="var(--footer-line)"/>
    <rect class="footer" x="0" y="1305" width="1057" height="116" fill="var(--footer-blue)"/>
  </svg>
</div>
</body>
</html>
```